Corvel Capital LLC

Need Professional Business cards for New Investment Fund

Target Market(s)

High Quality investors

Industry/Entity Type

Financial

Contact Information for Business Card

Phone Number +1 555 284 6190
Name Lukas Varenko
Title Fund Manager
email lv@FundCorvel.com
Website www.FundCorvel.com

Colors

Designer to choose colors to be used in the design.

Requirements
Must have
• Must have our Logo and all of the above. Must be made so lettering and loge can be raised

```html
<!DOCTYPE html>
<html lang="en">
<head>
<meta charset="utf-8">
<title>Telvarin – Business Card</title>
<link rel="stylesheet" href="https://fonts.googleapis.com/css2?family=Roboto:wght@400;500;700&display=swap">
<style>
  :root {
    --backdrop: #3b3b3b;
    --card: #1f1f21;
    --accent: #8cc21a;
    --white: #f4f4f4;
    --emboss: #8a8a8a;
  }
  * { margin: 0; padding: 0; box-sizing: border-box; }
  html, body {
    width: 799px;
    height: 1200px;
    overflow: hidden;
    background: var(--backdrop);
    font-family: "Roboto", Arial, sans-serif;
  }
  .sheet {
    position: relative;
    width: 799px;
    height: 1200px;
  }
  .card {
    position: absolute;
    left: 90px;
    width: 620px;
    height: 354px;
    background: var(--card);
    border-radius: 4px;
    box-shadow: 0 10px 28px rgba(0, 0, 0, 0.45);
  }
  .card--front { top: 110px; }
  .card--back  { top: 700px; }

  /* Front: centred wordmark */
  .front-mark {
    position: absolute;
    inset: 0;
    display: flex;
    align-items: center;
    justify-content: center;
    gap: 14px;
  }
  .front-mark__dot {
    width: 18px;
    height: 18px;
    background: var(--emboss);
  }
  .front-mark__name {
    font-weight: 500;
    font-size: 40px;
    letter-spacing: 2px;
    color: var(--emboss);
    white-space: nowrap;
  }

  /* Back: person */
  .person {
    position: absolute;
    left: 40px;
    top: 38px;
  }
  .person__name {
    font-weight: 700;
    font-size: 22px;
    color: var(--accent);
  }
  .person__title {
    margin-top: 4px;
    font-size: 13px;
    color: var(--white);
  }

  /* Back: contacts */
  .contacts {
    position: absolute;
    left: 40px;
    bottom: 44px;
    list-style: none;
  }
  .contacts__item {
    display: flex;
    align-items: center;
    gap: 14px;
    font-size: 15px;
    color: var(--white);
    line-height: 26px;
    white-space: nowrap;
  }
  .contacts__icon {
    width: 14px;
    height: 14px;
    fill: var(--accent);
    flex: none;
  }

  /* Back: wordmark */
  .back-mark {
    position: absolute;
    right: 44px;
    bottom: 96px;
    display: flex;
    align-items: center;
    gap: 14px;
  }
  .back-mark__square {
    width: 22px;
    height: 22px;
    background: var(--accent);
  }
  .back-mark__name {
    font-weight: 500;
    font-size: 34px;
    letter-spacing: 2px;
    color: var(--white);
    white-space: nowrap;
  }
</style>
</head>
<body>
<main class="sheet">
  <section class="card card--front" aria-label="Card front">
    <div class="front-mark">
      <span class="front-mark__dot"></span>
      <span class="front-mark__name">TELVARIN</span>
    </div>
  </section>

  <section class="card card--back" aria-label="Card back">
    <div class="person">
      <p class="person__name">Lukas Varenko</p>
      <p class="person__title">Fund Manager</p>
    </div>

    <ul class="contacts">
      <li class="contacts__item">
        <svg class="contacts__icon" viewBox="0 0 16 16" aria-hidden="true"><path d="M3 1h3l1.5 4-2 1.3a9 9 0 0 0 4.2 4.2L11 8.5l4 1.5v3a2 2 0 0 1-2 2A13 13 0 0 1 1 3a2 2 0 0 1 2-2z"/></svg>
        +1 555 284 6190
      </li>
      <li class="contacts__item">
        <svg class="contacts__icon" viewBox="0 0 16 16" aria-hidden="true"><path d="M1 3h14v10H1z"/><path d="M1.5 3.8 8 9l6.5-5.2" stroke="#1f1f21" stroke-width="1.2" fill="none"/></svg>
        lv@FundCorvel.com
      </li>
      <li class="contacts__item">
        <svg class="contacts__icon" viewBox="0 0 16 16" aria-hidden="true"><circle cx="8" cy="8" r="7"/><path d="M1 8h14M8 1c-3 3.5-3 10.5 0 14M8 1c3 3.5 3 10.5 0 14" stroke="#1f1f21" stroke-width="1" fill="none"/></svg>
        www.FundCorvel.com
      </li>
    </ul>

    <div class="back-mark">
      <span class="back-mark__square"></span>
      <span class="back-mark__name">TELVARIN</span>
    </div>
  </section>
</main>
</body>
</html>
```